Bry7Legal Letterhead

Need a new letterhead for my law firm.
IDENTIFYING INFORMATION BELOW:
Anselmo R Quintara III
Attorney at Law
Address: 2847 Larkspur Blvd, Ste 300, Dallas, TX 75204
Phone: 877-482-6017
Fax: 469-738-1452
Email: bry@bry7legal.example
Website: www.bry7legal.example

Colors
0054AA
0677BA
7BADD7
CADEEF
E8F1F8

Requirements
Must have
• Logo needs to be on the letterhead, along with identifying information which is included in the project description.

```html
<!DOCTYPE html>
<html lang="en">
<head>
<meta charset="utf-8">
<title>Bry7Legal Letterhead</title>
<link href="https://fonts.googleapis.com/css2?family=Lato:wght@400;700;900&family=Open+Sans:wght@400&display=swap" rel="stylesheet">
<style>
  :root {
    --ink: #111111;
    --text: #3a3a3a;
    --brand-blue: #0054AA;
    --brand-mid: #0677BA;
    --brand-light: #7BADD7;
    --brand-pale: #CADEEF;
    --rule: #9a9a9a;
    --paper: #ffffff;
    --footer: #000000;
  }
  html, body {
    margin: 0;
    padding: 0;
    width: 1040px;
    height: 1200px;
    overflow: hidden;
    background: var(--paper);
  }
  .letterhead {
    position: relative;
    width: 1040px;
    height: 1200px;
    background: var(--paper);
    font-family: "Open Sans", Arial, sans-serif;
    color: var(--text);
  }
  .brand {
    position: absolute;
    left: 102px;
    top: 42px;
    width: 262px;
    text-align: center;
  }
  .brand-name {
    display: block;
    font-family: "Lato", Arial, sans-serif;
    font-weight: 900;
    font-size: 38px;
    letter-spacing: 2px;
    color: var(--ink);
    line-height: 1;
  }
  .brand-tagline {
    display: block;
    margin-top: 5px;
    font-family: "Lato", Arial, sans-serif;
    font-size: 15px;
    letter-spacing: 2.5px;
    color: var(--ink);
  }
  .contact {
    position: absolute;
    left: 700px;
    top: 22px;
    height: 136px;
    padding-left: 17px;
    border-left: 1.5px solid var(--rule);
    font-family: "Lato", Arial, sans-serif;
    font-style: normal;
    color: var(--ink);
  }
  .contact-name {
    margin: 0;
    font-size: 21px;
    font-weight: 700;
    color: var(--brand-blue);
    line-height: 26px;
  }
  .contact-title {
    margin: 0 0 4px;
    font-size: 18px;
    line-height: 24px;
  }
  .contact-list {
    list-style: none;
    margin: 0;
    padding: 0;
    font-size: 18px;
    line-height: 22px;
  }
  .contact-list li {
    display: flex;
    align-items: center;
    gap: 6px;
  }
  .contact-icon {
    width: 18px;
    height: 18px;
    flex: none;
    fill: var(--brand-mid);
  }
  .letter {
    position: absolute;
    left: 98px;
    top: 234px;
    width: 838px;
    font-size: 15px;
    line-height: 27px;
  }
  .letter p { margin: 0; }
  .issue-date { margin-bottom: 18px !important; }
  .recipient { line-height: 18px; }
  .salutation { margin-top: 50px !important; }
  .body-copy {
    margin-top: 26px !important;
    text-align: justify;
    hyphens: auto;
  }
  .body-copy + .body-copy { margin-top: 27px !important; }
  .closing { margin-top: 54px !important; }
  .signature-mark {
    display: block;
    margin: 12px 0 8px;
    width: 214px;
    height: 26px;
    background: linear-gradient(90deg, #d8d8d8, #c4c4c4);
    border-radius: 3px;
  }
  .signer-name {
    font-size: 19px;
    color: #222;
    line-height: 26px;
  }
  .signer-role { line-height: 24px; }
  .footer-band {
    position: absolute;
    left: 0;
    bottom: 0;
    width: 1040px;
    height: 104px;
    background: var(--footer);
  }
  .footer-accent {
    position: absolute;
    left: 0;
    bottom: 104px;
    width: 1040px;
    height: 10px;
    background: linear-gradient(90deg, var(--brand-blue), var(--brand-mid) 60%, var(--brand-light));
  }
  .footer-rule {
    position: absolute;
    left: 0;
    bottom: 120px;
    width: 1040px;
    height: 3px;
    background: var(--brand-pale);
  }
  .footer-address {
    position: absolute;
    right: 94px;
    bottom: 38px;
    margin: 0;
    font-family: "Lato", Arial, sans-serif;
    font-size: 18px;
    color: #ffffff;
  }
</style>
</head>
<body>
  <main class="letterhead">
    <div class="brand">
      <span class="brand-name">BRY7LEGAL</span>
      <span class="brand-tagline">COUNSEL YOU CAN TRUST</span>
    </div>

    <address class="contact">
      <p class="contact-name">Anselmo R Quintara III</p>
      <p class="contact-title">Attorney at Law</p>
      <ul class="contact-list">
        <li>
          <svg class="contact-icon" viewBox="0 0 24 24" aria-hidden="true"><path d="M2 9c0-3 4-5 10-5s10 2 10 5l-1 2h-4l-1-3H8l-1 3H3zM6 12h12l3 8H3z"/></svg>
          877-482-6017
        </li>
        <li>
          <svg class="contact-icon" viewBox="0 0 24 24" aria-hidden="true"><path d="M6 2h12v6H6zM2 9h20v9h-4v-4H6v4H2zM7 15h10v7H7z"/></svg>
          469-738-1452
        </li>
        <li>
          <svg class="contact-icon" viewBox="0 0 24 24" aria-hidden="true"><path d="M2 5h20v14H2zM4 7v1l8 6 8-6V7l-8 6z" fill-rule="evenodd"/></svg>
          bry@bry7legal.example
        </li>
        <li>
          <svg class="contact-icon" viewBox="0 0 24 24" aria-hidden="true"><circle cx="12" cy="12" r="10"/><path d="M2 12h20M12 2c3 3 3 17 0 20M12 2c-3 3-3 17 0 20" stroke="#fff" stroke-width="1.4" fill="none"/></svg>
          www.bry7legal.example
        </li>
      </ul>
    </address>

    <article class="letter">
      <p class="issue-date">Issuing Date: May 5, 2018</p>
      <p class="recipient">Name Of Employee Mr. XYZABC<br>Address of Employee<br>Address Line 2 etc..</p>
      <p class="salutation">Dear Mr.XYZABC</p>
      <p class="body-copy">Lorem Ipsum has been the industry's standard dummy text ever since the 1500s, when an unknown printer took a galley of type and scrambled it to make a type specimen book. It has survived not only five centuries, but also the leap into electronic typesetting, remaining essentially unchanged. It was popularised in the 1960s with the release of Typemark sheets containing Lorem Ipsum passages, and more recently with desktop publishing software like Quillset Composer including versions of Lorem Ipsum.</p>
      <p class="body-copy">Lorem Ipsum is simply dummy text of the printing and typesetting industry. Lorem Ipsum has been the industry's standard dummy text ever since the 1500s, when an unknown printer took a galley of type and scrambled it to make a type specimen book.</p>
      <p class="body-copy">It has survived not only five centuries, but also the leap into electronic typesetting, remaining essentially unchanged. It was popularised in the 1960s with the release of Typemark sheets containing Lorem IpsumIpsum passages.</p>
      <p class="closing">Yours Sincerely</p>
      <span class="signature-mark" role="img" aria-label="Handwritten signature of Marten Ellory"></span>
      <p class="signer-name">Marten Ellory</p>
      <p class="signer-role">Managing Director</p>
    </article>

    <footer>
      <div class="footer-rule"></div>
      <div class="footer-accent"></div>
      <div class="footer-band"></div>
      <p class="footer-address">2847 Larkspur Blvd, Ste 300, Dallas, TX 75204</p>
    </footer>
  </main>
</body>
</html>
```